business card - Helicopter Flight Services, Flight School, etc.

We need a business card design for a new helicopter service.

We offer Helicopter Flight Services, Aerial Filming & Photography, Flight School, and Helicopter Tours. In that order.

Summit BladeAir, Inc.
Dennis Tollerby
SummitBladeair@Kestmail.com
626-418-7352

Based at the Brenwick Airport in Van Nuys, CA. The final design should communicate integrity and safety. Pictures or logos at your discretion.

Card back side - surprise me.

```html
<!DOCTYPE html>
<html lang="en">
<head>
<meta charset="utf-8">
<title>Summit BladeAir, Inc. — Business Card</title>
<link rel="stylesheet" href="https://fonts.googleapis.com/css2?family=Open+Sans:wght@400;600;700&display=swap">
<style>
  :root {
    --backdrop: #3a322d;
    --card: #16181b;
    --card-edge: #202327;
    --blue: #1a8fe8;
    --white: #f2f4f6;
    --muted: #9aa3ab;
  }
  * { box-sizing: border-box; margin: 0; padding: 0; }
  html, body {
    width: 1200px; height: 844px; overflow: hidden;
    background: var(--backdrop);
    font-family: "Open Sans", Arial, sans-serif;
  }
  .canvas { position: relative; width: 1200px; height: 844px; }
  .card {
    position: absolute;
    width: 540px; height: 309px;
    background: linear-gradient(160deg, var(--card-edge), var(--card));
    border-radius: 4px;
    box-shadow: 0 10px 24px rgba(0,0,0,.45);
    overflow: hidden;
  }
  .card--front { left: 50px; top: 440px; }
  .card--back { left: 610px; top: 100px; }

  /* Front */
  .brand {
    position: absolute; left: 40px; top: 70px;
    display: flex; align-items: center; gap: 12px;
  }
  .brand__mark {
    width: 22px; height: 22px; border-radius: 50%;
    background: var(--blue);
  }
  .brand__name {
    font-weight: 600; font-size: 20px; color: var(--blue);
    letter-spacing: .5px;
  }
  .divider {
    position: absolute; left: 0; right: 200px; top: 232px;
    height: 1px; background: var(--blue); opacity: .8;
  }
  .contact {
    position: absolute; right: 28px; top: 170px;
    text-align: right;
  }
  .contact__name {
    font-weight: 700; font-size: 19px; color: var(--blue);
    margin-bottom: 8px;
  }
  .contact__line {
    display: flex; justify-content: flex-end; align-items: center; gap: 8px;
    font-size: 13px; color: var(--white); line-height: 22px;
  }
  .contact__icon { width: 11px; height: 11px; fill: var(--blue); }

  /* Back */
  .services {
    position: absolute; left: 56px; top: 130px;
    list-style: none;
  }
  .services__item {
    display: flex; align-items: center; gap: 12px;
    font-size: 14px; color: var(--white); line-height: 25px;
  }
  .services__item::before {
    content: ""; width: 8px; height: 8px; border-radius: 50%;
    background: var(--blue);
  }
  .back-accent {
    position: absolute; right: -70px; top: -70px;
    width: 210px; height: 210px; border-radius: 50%;
    border: 6px solid var(--blue);
  }
</style>
</head>
<body>
<main class="canvas">
  <section class="card card--front" aria-label="Card front">
    <div class="brand">
      <span class="brand__mark"></span>
      <span class="brand__name">Summit BladeAir, Inc.</span>
    </div>
    <div class="divider"></div>
    <div class="contact">
      <p class="contact__name">Dennis Tollerby</p>
      <p class="contact__line">626-418-7352
        <svg class="contact__icon" viewBox="0 0 24 24" aria-hidden="true"><path d="M6.6 10.8a15.1 15.1 0 0 0 6.6 6.6l2.2-2.2a1 1 0 0 1 1-.25 11.4 11.4 0 0 0 3.6.57 1 1 0 0 1 1 1V20a1 1 0 0 1-1 1A17 17 0 0 1 3 4a1 1 0 0 1 1-1h3.5a1 1 0 0 1 1 1c0 1.25.2 2.45.57 3.57a1 1 0 0 1-.25 1z"/></svg>
      </p>
      <p class="contact__line">SummitBladeair@Kestmail.com
        <svg class="contact__icon" viewBox="0 0 24 24" aria-hidden="true"><path d="M2 5h20v14H2z M2 5l10 8 10-8" fill="var(--blue)"/><path d="M3 6l9 7 9-7" fill="none" stroke="#16181b" stroke-width="2"/></svg>
      </p>
    </div>
  </section>

  <section class="card card--back" aria-label="Card back">
    <div class="back-accent"></div>
    <ul class="services">
      <li class="services__item">Flight School</li>
      <li class="services__item">Helicopter Tours</li>
      <li class="services__item">Helicopter Flight Services</li>
      <li class="services__item">Aerial Filming &amp; Photography</li>
    </ul>
  </section>
</main>
</body>
</html>
```